Flyer for Commercial Roofing Company

We are seeking a talented graphic designer to create a high-quality, visually appealing bifold brochure for Brackenvale Roofing, a certified commercial roofing company specializing in apartment communities. The brochure will be 8.5x11 inches when folded and 17x11 inches when open, containing a front cover, two inside pages, and a back cover. The content is already developed, highlighting our services, key features, and contact information. The design should incorporate professional imagery of multifamily properties, modern icons, a clean layout, and our brand colors and logo to convey trust, expertise, and innovation. The goal is to produce a compelling marketing piece that engages property managers and decision-makers.
Target Market(s)
Apartment Communites
Look and feel
Each slider illustrates characteristics of the customer's brand and the style your logo design should communicate.

```html
<!DOCTYPE html>
<html lang="en">
<head>
<meta charset="utf-8">
<title>Brackenvale Roofing – Bifold Brochure</title>
<link href="https://fonts.googleapis.com/css2?family=Montserrat:wght@500;600;700;800;900&family=Open+Sans:wght@400;600;700&display=swap" rel="stylesheet">
<style>
:root{
  --red:#b8141d;
  --red-dark:#8f0d14;
  --navy:#1b2241;
  --navy-2:#262f57;
  --ink:#2b2f3a;
  --muted:#5b6070;
  --paper:#ffffff;
  --soft:#f3f4f7;
  --stage:#d8d9db;
  --head:'Montserrat',Arial,sans-serif;
  --body:'Open Sans',Arial,sans-serif;
}
*{box-sizing:border-box;margin:0;padding:0}
html,body{width:1200px;height:2400px;overflow:hidden;background:var(--stage)}
body{position:relative;font-family:var(--body);color:var(--ink)}
.spread{position:absolute;left:20px;width:1160px;height:750px;display:flex;box-shadow:0 6px 18px rgba(0,0,0,.18)}
.spread--outside{top:330px}
.spread--inside{top:1240px}
.panel{position:relative;width:580px;height:750px;overflow:hidden;background:var(--paper)}
.abs{position:absolute}
.photo{position:absolute}
h1,h2,h3,h4{font-family:var(--head)}
/* ---------- back cover ---------- */
.back{background:var(--navy)}
.back__title{left:36px;top:34px;color:#fff;font-size:17px;font-weight:700}
.quote{left:0;top:66px;width:330px;height:150px;background:var(--red);padding:20px 24px 0 74px;color:#fff}
.quote__mark{position:absolute;left:22px;top:4px;font-family:var(--head);font-size:70px;font-weight:900;line-height:1}
.quote p{font-size:12.5px;line-height:1.5}
.quote cite{display:block;margin-top:10px;font-style:normal;font-weight:700;font-size:11.5px}
.back__slash{left:0;top:250px}
.back__photo{left:150px;top:180px;width:395px;height:250px;border:7px solid #fff;background:linear-gradient(160deg,#dfe6ee 0%,#b9c3cc 45%,#6e6458 100%)}
.cta{left:36px;top:466px;background:var(--red);color:#fff;font-family:var(--head);font-weight:800;font-size:18px;padding:8px 22px;border-radius:4px;letter-spacing:.5px}
.cta-copy{left:36px;top:516px;width:300px;color:#fff;font-size:13px;line-height:1.5}
.cta-copy strong{font-family:var(--head);display:block;font-size:15px}
.contacts{left:36px;top:584px;list-style:none;color:#fff;font-size:12.5px}
.contacts li{display:flex;align-items:center;gap:10px;margin-bottom:9px}
.contacts svg{width:22px;height:22px;flex:none}
.back__bar{left:0;bottom:0;width:580px;height:50px;background:var(--red);color:#fff;font-family:var(--head);font-weight:700;font-size:14px;display:flex;align-items:center;justify-content:center}
/* ---------- front cover ---------- */
.brand{left:36px;top:30px;display:flex;align-items:center;gap:12px}
.brand__mark{width:34px;height:34px;background:var(--red)}
.brand__name{font-family:var(--head);font-weight:800;font-size:20px;color:var(--navy);letter-spacing:.5px;text-transform:uppercase;line-height:1.05;width:160px}
.front__corner{right:0;top:0}
.front__photo{left:36px;top:104px;width:508px;height:330px;border:6px solid var(--navy);background:linear-gradient(180deg,#aac7e4 0%,#d6e2ee 48%,#8a8f96 70%,#5f7d4a 100%)}
.front__kicker{left:36px;top:458px;color:var(--navy);font-family:var(--head);font-weight:600;font-size:14px}
.front__headline{left:36px;top:482px;width:400px;font-family:var(--head);font-weight:900;font-size:30px;line-height:1.08;color:var(--red);text-transform:uppercase}
.front__headline span{color:var(--navy)}
.features{left:36px;top:586px;display:flex;gap:18px;list-style:none}
.features li{display:flex;align-items:center;gap:7px;font-size:10.5px;font-weight:600;color:var(--navy);width:118px;line-height:1.25}
.features svg{width:28px;height:28px;flex:none}
.badge{right:40px;top:462px}
.front__bar{left:0;bottom:0;width:580px;height:50px;background:var(--navy);color:#fff;font-size:13px;font-weight:600;display:flex;align-items:center;justify-content:center;border-top:5px solid var(--red)}
/* ---------- inside left ---------- */
.why{left:0;top:0;width:580px;height:190px}
.why__title{left:30px;top:22px;width:270px;color:#fff;font-size:21px;font-weight:800;line-height:1.15}
.why__text{left:30px;top:108px;width:265px;color:#fff;font-size:11px;line-height:1.5}
.why__photo{left:318px;top:22px;width:236px;height:150px;border:5px solid #fff;background:linear-gradient(150deg,#6c7480 0%,#3f4652 60%,#8fa0b0 100%)}
.spec__title{left:30px;top:206px;font-size:17px;font-weight:800;color:var(--navy)}
.specs{left:30px;top:236px;display:flex;gap:14px}
.spec{width:164px;height:108px;border:1.5px solid #d6d9e1;border-top:4px solid var(--red);border-radius:6px;background:#fff;padding:9px 8px;text-align:center}
.spec svg{width:30px;height:30px}
.spec h4{font-size:11px;color:var(--red);margin-top:4px;line-height:1.25}
.spec p{font-size:9px;color:var(--muted);line-height:1.35;margin-top:3px}
.sol__title{left:30px;top:366px;font-size:32px;font-weight:900;color:var(--navy);line-height:1.05}
.sol__title span{color:var(--red)}
.solutions{left:30px;top:456px;width:520px;display:grid;grid-template-columns:1fr 1fr;gap:16px 24px;list-style:none}
.solution{display:flex;gap:10px;align-items:center}
.solution .thumb{position:relative;width:84px;height:58px;flex:none;border-radius:4px;background:linear-gradient(135deg,#9aa3ad,#5c6571)}
.solution h4{font-size:13px;color:var(--navy)}
.solution p{font-size:9.5px;color:var(--muted);line-height:1.35}
.in-left__bar{left:0;bottom:0;width:580px;height:36px;background:var(--navy);color:#fff;font-size:10.5px;display:flex;align-items:center;justify-content:space-around}
/* ---------- inside right ---------- */
.svc__rule{left:30px;top:34px;width:6px;height:44px;background:var(--red)}
.svc__title{left:46px;top:30px;font-size:24px;font-weight:800;color:var(--navy);line-height:1.05;width:120px}
.svc__intro{left:190px;top:38px;width:350px;font-size:12px;line-height:1.5;color:var(--muted)}
.services{left:30px;top:116px;width:520px;display:grid;grid-template-columns:1fr 1fr;gap:26px 22px;list-style:none}
.service{display:flex;gap:10px}
.service .thumb{position:relative;width:104px;height:86px;flex:none;border-radius:4px;background:linear-gradient(135deg,#a3734f,#5a4a40)}
.service h4{font-size:13px;color:var(--red);margin:4px 0 4px}
.service p{font-size:10px;line-height:1.45;color:var(--muted)}
.emergency{left:0;top:600px;width:580px;height:150px}
.emergency__text{left:150px;top:640px;width:330px;color:#fff}
.emergency__text h4{font-size:17px;font-weight:800}
.emergency__text p{font-size:11.5px;line-height:1.45;margin-top:4px}
.emergency__icon{left:60px;top:636px}
</style>
</head>
<body>

<section class="spread spread--outside" aria-label="Brochure outside spread">
  <article class="panel back">
    <h3 class="abs back__title">What Our Clients Say</h3>
    <svg class="abs back__slash" width="580" height="260" viewBox="0 0 580 260" aria-hidden="true">
      <polygon points="0,0 130,0 0,170" fill="var(--red-dark)"/>
      <polygon points="0,180 580,120 580,170 0,230" fill="var(--navy-2)"/>
    </svg>
    <blockquote class="abs quote">
      <span class="quote__mark">“</span>
      <p>Brackenvale Roofing's expertise and professionalism made all the difference for our property.</p>
      <cite>– Dana R., Property Manager</cite>
    </blockquote>
    <div class="photo back__photo" role="img" aria-label="Photo of a couple standing outside a modern apartment home"></div>
    <div class="abs cta">GET IN TOUCH</div>
    <p class="abs cta-copy">Ready to protect your property with the best in roofing? <strong>Contact us today!</strong></p>
    <ul class="abs contacts">
      <li><svg viewBox="0 0 24 24"><circle cx="12" cy="12" r="12" fill="var(--red)"/><path d="M8.5 6.5l2 2-1.2 1.6a7 7 0 0 0 4.6 4.6l1.6-1.2 2 2-1.4 1.8c-4.8-.4-8.8-4.4-9.2-9.2z" fill="#fff"/></svg>(555) 014-2280</li>
      <li><svg viewBox="0 0 24 24"><circle cx="12" cy="12" r="12" fill="var(--red)"/><rect x="6" y="8" width="12" height="8" fill="#fff"/><path d="M6 8l6 5 6-5" stroke="var(--red)" stroke-width="1.3" fill="none"/></svg>hello@brackenvaleroofing.com</li>
      <li><svg viewBox="0 0 24 24"><circle cx="12" cy="12" r="12" fill="var(--red)"/><circle cx="12" cy="12" r="6" fill="none" stroke="#fff" stroke-width="1.4"/><path d="M6 12h12M12 6c-3 3-3 9 0 12M12 6c3 3 3 9 0 12" stroke="#fff" stroke-width="1.2" fill="none"/></svg>www.brackenvaleroofing.com</li>
    </ul>
    <div class="abs back__bar">Request a Free Roof Inspection Today</div>
  </article>

  <article class="panel front">
    <svg class="abs front__corner" width="200" height="90" viewBox="0 0 200 90" aria-hidden="true">
      <polygon points="60,0 200,0 200,90" fill="var(--navy)"/>
      <polygon points="120,0 200,0 200,50" fill="var(--red)"/>
    </svg>
    <div class="abs brand">
      <span class="brand__mark"></span>
      <span class="brand__name">Brackenvale Roofing</span>
    </div>
    <div class="photo front__photo" role="img" aria-label="Photo of a two-storey modern residential building with a grey roof"></div>
    <p class="abs front__kicker">Protecting Apartment Communities with</p>
    <h1 class="abs front__headline">Precision Roofing <span>Solutions</span></h1>
    <ul class="abs features">
      <li><svg viewBox="0 0 28 28"><circle cx="14" cy="14" r="14" fill="var(--red)"/><path d="M8 14l4 4 8-8" stroke="#fff" stroke-width="2.4" fill="none"/></svg>Certified Contractor</li>
      <li><svg viewBox="0 0 28 28"><circle cx="14" cy="14" r="14" fill="var(--red)"/><path d="M8 14l4 4 8-8" stroke="#fff" stroke-width="2.4" fill="none"/></svg>Long-Term Warranty</li>
      <li><svg viewBox="0 0 28 28"><circle cx="14" cy="14" r="14" fill="var(--red)"/><path d="M8 14l4 4 8-8" stroke="#fff" stroke-width="2.4" fill="none"/></svg>24/7 Emergency Care</li>
    </ul>
    <svg class="abs badge" width="96" height="112" viewBox="0 0 96 112" aria-hidden="true">
      <path d="M48 2L92 16v40c0 28-20 46-44 54C24 102 4 84 4 56V16z" fill="var(--red)"/>
      <path d="M48 12L82 23v33c0 22-15 37-34 44C29 93 14 78 14 56V23z" fill="none" stroke="#fff" stroke-width="2"/>
    </svg>
    <div class="abs front__bar">www.brackenvaleroofing.com</div>
  </article>
</section>

<section class="spread spread--inside" aria-label="Brochure inside spread">
  <article class="panel in-left">
    <svg class="abs why" viewBox="0 0 580 190" aria-hidden="true">
      <polygon points="0,0 580,0 580,150 0,190" fill="var(--red)"/>
    </svg>
    <h2 class="abs why__title">Why Choose Brackenvale Roofing?</h2>
    <p class="abs why__text">Certified crews and clear reporting, built for apartment communities and their managers.</p>
    <div class="photo why__photo" role="img" aria-label="Photo of a dark commercial roof with a crew at work"></div>

    <h3 class="abs spec__title">Our specialties</h3>
    <div class="abs specs">
      <div class="spec"><svg viewBox="0 0 30 30"><circle cx="15" cy="15" r="14" fill="none" stroke="var(--navy)" stroke-width="2"/><path d="M9 15l4 4 8-8" stroke="var(--red)" stroke-width="2.4" fill="none"/></svg><h4>Certified Roofing Contractor</h4><p>Factory trained crews on every job.</p></div>
      <div class="spec"><svg viewBox="0 0 30 30"><path d="M15 2l11 4v9c0 7-5 11-11 13C9 26 4 22 4 15V6z" fill="none" stroke="var(--navy)" stroke-width="2"/><path d="M10 15l3 3 7-7" stroke="var(--red)" stroke-width="2.4" fill="none"/></svg><h4>25+ Year Warranty</h4><p>Coverage that protects your budget.</p></div>
      <div class="spec"><svg viewBox="0 0 30 30"><rect x="6" y="3" width="18" height="24" rx="2" fill="none" stroke="var(--navy)" stroke-width="2"/><path d="M10 10h10M10 15h10M10 20h6" stroke="var(--red)" stroke-width="2"/></svg><h4>Licensed &amp; Compliant</h4><p>Fully insured and code ready work.</p></div>
    </div>

    <h2 class="abs sol__title">Our Roofing<br><span>Solutions</span></h2>
    <ul class="abs solutions">
      <li class="solution"><div class="thumb" role="img" aria-label="Photo of a white TPO membrane roof"></div><div><h4>TPO Roofing</h4><p>Energy efficient, reflective membrane.</p></div></li>
      <li class="solution"><div class="thumb" role="img" aria-label="Photo of a PVC roof surface"></div><div><h4>PVC Roofing</h4><p>Durable, chemical resistant system.</p></div></li>
      <li class="solution"><div class="thumb" role="img" aria-label="Photo of a black EPDM rubber roof"></div><div><h4>EPDM Roofing</h4><p>Flexible rubber for flat roofs.</p></div></li>
      <li class="solution"><div class="thumb" role="img" aria-label="Photo of asphalt shingles"></div><div><h4>Asphalt Shingles</h4><p>Classic, cost effective protection.</p></div></li>
      <li class="solution"><div class="thumb" role="img" aria-label="Photo of a metal roof"></div><div><h4>Metal Roofing</h4><p>Long lasting, low upkeep panels.</p></div></li>
      <li class="solution"><div class="thumb" role="img" aria-label="Photo of a roof coating being applied"></div><div><h4>Roof Coatings</h4><p>Extend roof life, cut energy costs.</p></div></li>
    </ul>
    <div class="abs in-left__bar"><span>(555) 014-2280</span><span>hello@brackenvaleroofing.com</span><span>www.brackenvaleroofing.com</span></div>
  </article>

  <article class="panel in-right">
    <div class="abs svc__rule"></div>
    <h2 class="abs svc__title">Our Services</h2>
    <p class="abs svc__intro">We offer comprehensive roofing solutions for every stage of your roof's lifecycle.</p>
    <ul class="abs services">
      <li class="service"><div class="thumb" role="img" aria-label="Photo of a roofer repairing shingles"></div><div><h4>Roof Repairs</h4><p>Fast, reliable fixes to stop leaks and prevent further damage.</p></div></li>
      <li class="service"><div class="thumb" role="img" aria-label="Photo of a roof inspection"></div><div><h4>Roof Inspections</h4><p>Thorough assessments to identify potential issues early.</p></div></li>
      <li class="service"><div class="thumb" role="img" aria-label="Photo of roof maintenance work"></div><div><h4>Preventative Maintenance</h4><p>Keep your roof in optimal condition year round.</p></div></li>
      <li class="service"><div class="thumb" role="img" aria-label="Photo of a new roof installation"></div><div><h4>New Roof Installations</h4><p>High quality installations with certified materials.</p></div></li>
    </ul>
    <svg class="abs emergency" viewBox="0 0 580 150" aria-hidden="true">
      <polygon points="0,30 580,0 580,150 0,150" fill="var(--navy)"/>
      <polygon points="0,30 160,22 0,80" fill="var(--red)"/>
      <polygon points="460,150 580,90 580,150" fill="var(--red)"/>
    </svg>
    <svg class="abs emergency__icon" width="64" height="64" viewBox="0 0 64 64" aria-hidden="true">
      <circle cx="32" cy="32" r="30" fill="var(--red)"/>
      <path d="M22 19l6 6-3.5 4.5a19 19 0 0 0 10 10L39 36l6 6-4 5c-12-1-21-10-22-22z" fill="#fff"/>
    </svg>
    <div class="abs emergency__text">
      <h4>Emergency Services</h4>
      <p>24/7 rapid response to urgent roofing issues.</p>
    </div>
  </article>
</section>

</body>
</html>
```